Breakfast Cafe - The Sunny Nook

It is for my breakfast and lunch cafe with a hawaiian / beach theme. I am open 7 days a week from 7am to 2pm. We serve traditional American food such as omelettes, pancakes, burgers and sandwiches. I'll upload my old card and my new logo to be used. We have a lot of day to day regulars who eat there during the week, our t-shirts actually say 'Locals Only' on them. Hope this helps. Thanks.

Target Market(s)

anyone who has an appetite!

Industry/Entity Type

American Restaurant

Contact Information for Business Card

4815C Marlow Grove Avenue
Long Beach, California
(555) 731-2294

Requirements
Must have
• Address and phone number easily readable.
Nice to have
• beach or tropical theme

```html
<!DOCTYPE html>
<html lang="en">
<head>
<meta charset="utf-8">
<title>The Sunny Nook – Business Card</title>
<link href="https://fonts.googleapis.com/css2?family=Lato:ital,wght@0,400;0,700;1,400&display=swap" rel="stylesheet">
<style>
  :root {
    --stage: #000000;
    --card-light: #f3f3f3;
    --card-blue: #5bbfd6;
    --brand-rust: #b0560f;
    --ink: #1a1a1a;
    --badge: #f4a340;
  }
  html, body {
    margin: 0;
    padding: 0;
    width: 1200px;
    height: 900px;
    overflow: hidden;
    background: var(--stage);
    font-family: "Lato", Arial, sans-serif;
  }
  .canvas {
    position: relative;
    width: 1200px;
    height: 900px;
  }
  .card {
    position: absolute;
    top: 200px;
    width: 310px;
    height: 502px;
    overflow: hidden;
  }
  .card--front {
    left: 308px;
    background: var(--card-light);
    border-radius: 62px 0 62px 0;
  }
  .card--back {
    left: 641px;
    width: 309px;
    background: var(--card-blue);
    border-radius: 0 66px 0 66px;
  }
  .brand {
    position: absolute;
    left: 0;
    right: 0;
    text-align: center;
  }
  .brand__badge {
    display: block;
    margin: 0 auto;
    border-radius: 50%;
    background: var(--badge);
  }
  .brand__name {
    display: block;
    color: var(--brand-rust);
    font-weight: 700;
    white-space: nowrap;
  }
  .card--front .brand { top: 50px; left: 0; width: 226px; }
  .card--front .brand__badge { width: 118px; height: 118px; }
  .card--front .brand__name { font-size: 24px; margin-top: 14px; }
  .card--back .brand { top: 48px; }
  .card--back .brand__badge { width: 150px; height: 150px; }
  .card--back .brand__name { font-size: 32px; margin-top: 18px; }

  .tagline {
    position: absolute;
    left: 27px;
    top: 244px;
    margin: 0;
    font-size: 21px;
    font-style: italic;
    color: var(--brand-rust);
    white-space: nowrap;
  }
  .contact {
    position: absolute;
    left: 25px;
    margin: 0;
    font-size: 18px;
    line-height: 23px;
    color: var(--ink);
  }
  .contact--phone { top: 309px; display: flex; align-items: center; gap: 5px; }
  .contact--phone svg { width: 19px; height: 19px; }
  .contact--address { top: 362px; font-style: normal; }
  .hours {
    position: absolute;
    left: 25px;
    top: 438px;
    margin: 0;
    font-size: 16px;
    color: var(--brand-rust);
    white-space: nowrap;
  }
  .menu {
    position: absolute;
    top: 302px;
    left: 0;
    right: 0;
    margin: 0;
    padding: 0;
    list-style: none;
    text-align: center;
    font-size: 25px;
    line-height: 37.5px;
    color: var(--brand-rust);
  }
</style>
</head>
<body>
<main class="canvas">
  <section class="card card--front" aria-label="Business card front">
    <div class="brand">
      <span class="brand__badge" aria-hidden="true"></span>
      <span class="brand__name">The Sunny Nook</span>
    </div>
    <p class="tagline">Family owned and operated!</p>
    <p class="contact contact--phone">
      <svg viewBox="0 0 20 20" aria-hidden="true">
        <rect width="20" height="20" rx="2" fill="#b0560f"/>
        <path d="M6.2 4.2c.5-.3 1.1-.2 1.4.3l1 1.8c.3.5.2 1-.2 1.4l-.8.7c.6 1.4 1.6 2.5 3 3.1l.7-.8c.4-.4 1-.5 1.4-.2l1.8 1c.5.3.6.9.3 1.4l-.6 1c-.5.7-1.4 1-2.2.7C8.6 13.5 6.5 11.4 5.4 8.1c-.3-.8 0-1.7.7-2.2z" fill="#ffffff"/>
      </svg>
      (555) 731-2294
    </p>
    <address class="contact contact--address">4815C Marlow Grove Avenue<br>Long Beach, California</address>
    <p class="hours">Breakfast &amp; Lunch 7am - 2pm Daily</p>
  </section>

  <section class="card card--back" aria-label="Business card back">
    <div class="brand">
      <span class="brand__badge" aria-hidden="true"></span>
      <span class="brand__name">The Sunny Nook</span>
    </div>
    <ul class="menu">
      <li>Omelettes</li>
      <li>Pancakes</li>
      <li>Burgers</li>
      <li>Sandwiches</li>
    </ul>
  </section>
</main>
</body>
</html>
```